Corvana Tongue Works, LLC

We need a business card that includes information about our business and conveys a reliable business that provides document translation services and interpreters for a variety of corporate and individual clients. We want to come across as professional, reliable, yet approachable. It should include the following on one side:

ESL / ENL Language Classes, Private Lessons, and Online Tutors
PLEXA Training and Testing
Translating & Interpreting Services
Contact us about Over-the-Phone Interpreting in over 200 languages
24/7/365
www.corvanatongue.example

The other side should include (555) 481-3062

Rhoda Pelling, President
482 Garnet Ave., Ste. 219
Indianapolis, IN 40917

Please add USA as part of the address. Also, please add rmpelling@corvanatongueworks.example as the e-mail address. Thank you.

Target Market(s)

Business professionals, their families, the international community

Industry/Entity Type

Business

Contact Information for Business Card

24/7/365
www.corvanatongue.example

(555) 481-3062

Rhoda Pelling, President
482 Garnet Ave., Ste. 219
Indianapolis, IN 40917
USA

Font styles to use
Sans Serif

Colors

Designer to choose colors to be used in the design.

Requirements
Must have
• See project description
• e-mail address and web address
• Phone number
Nice to have
• a globe
• physical address
Should not have
• Should not have the same color scheme as other agencies in our market in Indiana unless it is blue and black. No purple or yellow.

```html
<!DOCTYPE html>
<html lang="en">
<head>
<meta charset="utf-8">
<title>Corvana Tongue Works – Business Card</title>
<link rel="stylesheet" href="https://fonts.googleapis.com/css2?family=Lato:wght@400;700;900&display=swap">
<style>
  :root {
    --backdrop: #e7e4df;
    --card: #f6f6f6;
    --brand-blue: #258bca;
    --ink: #1c1c1c;
    --white: #ffffff;
    --map-tone: #e4e4e4;
  }
  * { box-sizing: border-box; margin: 0; padding: 0; }
  html, body { width: 1200px; height: 960px; overflow: hidden; }
  body {
    position: relative;
    background: var(--backdrop);
    font-family: "Lato", Arial, sans-serif;
    color: var(--ink);
  }
  .card {
    position: absolute;
    width: 600px;
    height: 341px;
    border-radius: 22px;
    background: var(--card);
    overflow: hidden;
    box-shadow: 0 3px 8px rgba(0,0,0,0.18);
  }
  .card--front { left: 302px; top: 130px; }
  .card--back  { left: 299px; top: 489px; width: 598px; }

  /* Front */
  .brand {
    position: absolute;
    left: 66px;
    top: 58px;
    display: flex;
    align-items: center;
    gap: 10px;
  }
  .brand__dot {
    width: 96px; height: 96px;
    border-radius: 50%;
    background: var(--brand-blue);
  }
  .brand__name {
    font-size: 24px;
    line-height: 28px;
    font-weight: 400;
    color: var(--ink);
  }
  .front-circle {
    position: absolute;
    left: 0; top: 0;
  }
  .contact {
    position: absolute;
    right: 44px;
    top: 176px;
    text-align: right;
    color: var(--white);
  }
  .contact__name { font-size: 21px; font-weight: 700; letter-spacing: 0.2px; line-height: 24px; }
  .contact__title { font-size: 14px; font-weight: 700; line-height: 18px; margin-bottom: 8px; }
  .contact__line { font-size: 13.5px; line-height: 17px; }
  .contact__phone { font-size: 13.5px; line-height: 17px; margin-top: 8px; }
  .contact__email { font-size: 12px; line-height: 17px; }

  /* Back */
  .world-map {
    position: absolute;
    left: 22px; top: 20px;
    width: 556px; height: 300px;
    border-radius: 40% 45% 35% 40%;
    background: radial-gradient(ellipse at 50% 45%, var(--map-tone) 0%, rgba(228,228,228,0.5) 55%, rgba(246,246,246,0) 75%);
  }
  .offer {
    position: absolute;
    left: 0; right: 0;
    top: 80px;
    text-align: center;
  }
  .offer__services { font-size: 15px; line-height: 19px; }
  .offer__callout {
    margin-top: 18px;
    font-size: 17px;
    font-weight: 900;
    line-height: 21px;
    text-transform: uppercase;
  }
  .offer__hours {
    margin-top: 18px;
    font-size: 19px;
    font-weight: 900;
    display: inline-flex;
    align-items: center;
    gap: 5px;
  }
  .offer__web { font-size: 17px; color: var(--brand-blue); margin-top: 4px; }
  .offer__web strong { font-weight: 900; }
</style>
</head>
<body>
  <section class="card card--front">
    <svg class="front-circle" width="600" height="341" viewBox="0 0 600 341" aria-hidden="true">
      <circle cx="593" cy="375" r="290" fill="var(--brand-blue)"/>
      <circle cx="593" cy="375" r="282" fill="none" stroke="var(--white)" stroke-width="3"/>
    </svg>
    <div class="brand">
      <span class="brand__dot"></span>
      <span class="brand__name">Corvana<br>Tongue<br>Works, LLC</span>
    </div>
    <div class="contact">
      <p class="contact__name">RHODA PELLING</p>
      <p class="contact__title">PRESIDENT</p>
      <p class="contact__line">482 Garnet Ave., Ste. 219</p>
      <p class="contact__line">Indianapolis, IN 40917</p>
      <p class="contact__line">USA</p>
      <p class="contact__phone">(555) 481-3062</p>
      <p class="contact__email">rmpelling@corvanatongueworks.example</p>
    </div>
  </section>

  <section class="card card--back">
    <div class="world-map" role="img" aria-label="Faint dotted world map in the background"></div>
    <div class="offer">
      <p class="offer__services">ESL / ENL Language Classes, Private Lessons, &amp; Online Tutors</p>
      <p class="offer__services">PLEXA Training &amp; Testing</p>
      <p class="offer__services">Translating &amp; Interpreting Services</p>
      <p class="offer__callout">Contact us about over-the-phone<br>interpreting in over 200 languages</p>
      <p class="offer__hours">
        <svg width="18" height="18" viewBox="0 0 18 18" aria-hidden="true">
          <circle cx="9" cy="9" r="7.5" fill="none" stroke="var(--ink)" stroke-width="1.6"/>
          <path d="M9 4.5V9L6.5 11.5" fill="none" stroke="var(--ink)" stroke-width="1.6" stroke-linecap="round"/>
        </svg>
        24/7/365
      </p>
      <p class="offer__web">www.<strong>CORVANATONGUE</strong>.example</p>
    </div>
  </section>
</body>
</html>
```